Small Business Consulting Firm Needs Letterhead

We need a letterhead for our company "Brightpath Plus". Our company does outbound calling and mailing to business owner's companies who have taken high interest loans. These loans tend to put these businesses in a big financial bind short term, and we help them find better financial options. We would like the design to match our colors of our logo. Headers and footers would look nice, but we are open. We would want it to include our address, website, phone, and email info. Our address - 2000 E. Lamar Blvd. Suite 600Website - www.safeguardtoday.comEmail - info@safeguardtoday.comPhone - 855-726-1938
Industry/Entity Type
Financial Planning
Look and feel
Each slider illustrates characteristics of the customer's brand and the style your logo design should communicate.

```html
<!DOCTYPE html>
<html lang="en">
<head>
<meta charset="utf-8">
<title>Brightpath Plus Letterhead</title>
<link rel="stylesheet" href="https://fonts.googleapis.com/css2?family=Montserrat:wght@400;500&display=swap">
<style>
  :root {
    --ink: #2b2b2b;
    --rule: #555555;
    --green: #74b843;
    --blue: #0b7fc2;
    --paper: #ffffff;
    --backdrop: #e6e6e4;
  }
  * { margin: 0; padding: 0; box-sizing: border-box; }
  html, body {
    width: 1200px; height: 1200px; overflow: hidden;
    background: var(--backdrop);
    font-family: "Montserrat", Arial, sans-serif;
    color: var(--ink);
  }
  .letterhead {
    position: absolute; left: 167px; top: 40px;
    width: 866px; height: 1120px;
    background: var(--paper);
    box-shadow: 0 6px 18px rgba(0,0,0,0.18);
    overflow: hidden;
  }
  .brand { position: absolute; left: 51px; top: 148px; display: flex; align-items: center; gap: 12px; }
  .brand-square { width: 22px; height: 22px; background: var(--green); }
  .brand-name { font-size: 25px; font-weight: 400; letter-spacing: 1.5px; color: var(--ink); text-transform: uppercase; }
  .contact {
    position: absolute; left: 579px; top: 84px;
    font-size: 15px; line-height: 20.5px; letter-spacing: 0.5px;
  }
  .contact-line { display: flex; align-items: center; gap: 7px; }
  .contact-icon { width: 13px; height: 13px; flex: none; }
  .header-rule { position: absolute; left: 52px; top: 205px; width: 762px; height: 1px; background: var(--rule); }
  .letter {
    position: absolute; left: 90px; width: 724px;
    font-size: 14.5px; letter-spacing: 0.9px; line-height: 23px;
  }
  .date { top: 304px; }
  .recipient { top: 363px; }
  .salutation { top: 484px; }
  .body-copy { top: 517px; line-height: 25.4px; text-align: justify; letter-spacing: 1px; }
  .body-copy p + p { margin-top: 14px; }
  .closing { top: 793px; }
  .signatory { top: 872px; line-height: 24px; }
  .signatory-name { font-size: 17px; font-weight: 500; letter-spacing: 0.8px; }
  .signatory-title { letter-spacing: 4px; }
  .footer-band { position: absolute; left: 0; bottom: 0; width: 866px; height: 40px; display: flex; }
  .footer-green { flex: 0 0 512px; background: var(--green); }
  .footer-blue { flex: 1; background: var(--blue); }
  .footer-url {
    position: absolute; right: 52px; bottom: 11px;
    color: #ffffff; font-size: 14.5px; letter-spacing: 1px;
  }
</style>
</head>
<body>
  <main class="letterhead">
    <div class="brand">
      <span class="brand-square"></span>
      <span class="brand-name">Brightpath Plus</span>
    </div>

    <div class="contact">
      <div>4170 W. Corwin Ave</div>
      <div>Suite 310</div>
      <div class="contact-line">
        <svg class="contact-icon" viewBox="0 0 16 16" aria-hidden="true"><path fill="#0b7fc2" d="M3.5 1.5l2.6 2.6-1.5 2a9 9 0 0 0 5.3 5.3l2-1.5 2.6 2.6-1.8 2C7.5 16 0 8.5 1.5 3.3z"/></svg>
        <span>855-726-1938</span>
      </div>
      <div class="contact-line">
        <svg class="contact-icon" viewBox="0 0 16 16" aria-hidden="true"><rect x="1" y="3" width="14" height="10" rx="1" fill="#0b7fc2"/><path d="M1.5 4l6.5 5 6.5-5" stroke="#fff" stroke-width="1.3" fill="none"/></svg>
        <span>info@brightpathplus.com</span>
      </div>
    </div>

    <div class="header-rule"></div>

    <div class="letter date">Date: 20 November 2018</div>

    <div class="letter recipient">
      To<br>
      Fernhollow Nursery Ltd.<br>
      58 Ashgrove Lane, Suite# B<br>
      Bristol, UK 4410B27
    </div>

    <div class="letter salutation">Dear Harlow,</div>

    <div class="letter body-copy">
      <p>Lorem Ipsum is simply dummy text of the printing and typesetting industry. Lorem Ipsum has been the industry's standard dummy text ever since the 1500s, when an unknown printer took a galley of type and scrambled it to make a type specimen book. It has survived not only five centuries, but also the leap into electronic typesetting, remaining essentially unchanged. It was popularised in the 1960s with the release of Typeline sheets containing Lorem Ipsum passages, and more recently with desktop publishing software like Pagecraft Studio including versions of Lorem Ipsum.</p>
      <p>Lorem Ipsum is simply dummy text of the printing and typesetting industry. Lorem Ipsum has been the industry's.</p>
    </div>

    <div class="letter closing">Thanking you</div>

    <div class="letter signatory">
      <div class="signatory-name">Marcus Lane Ellery</div>
      <div class="signatory-title">CEO</div>
    </div>

    <div class="footer-band" aria-hidden="true">
      <div class="footer-green"></div>
      <div class="footer-blue"></div>
    </div>
    <div class="footer-url">www.brightpathplus.com</div>
  </main>
</body>
</html>
```